I want ideas sample designs for my book cover

Hello,

We need a book cover designed in flat and 3D Versions. We would like to have jpg and png for final output and include a copy of the PSD for future revisions.

Here are the basic details:

Title: The Harvest of Quiet Builders
Author: Norman Quillfeather

Dimensions of book:

Was looking at the Pavo website for dimensions. I thought you may want to go on there and look at the different sizes. I used the 6x9” perfect bound US trade size for my book. You will see that this has a spine width of 0.225”, Cover size of 12.48 x 9.25” and spine begins at 6.125”

If you need background info on the author just to get an idea what he does, please check:

http://NormanQuillfeather.example

IMPORTANT: Please see attached document for a more detailed info:

Exact Title Of book
Back Cover
Spine Info
Measurements of book and dimension
Examples of book covers
Norman's photo attached

Thanks,
Darlene

Industry/Entity Type

Life Coaching

Font styles to use
Serif

Requirements
Must have
• Jpg, png and PSD files
• title
• author
• exact dimensions
• front and back cover
• flat and 3d versions

```html
<!DOCTYPE html>
<html lang="en">
<head>
<meta charset="utf-8">
<title>The Harvest of Quiet Builders – Cover Options</title>
<link rel="stylesheet" href="https://fonts.googleapis.com/css2?family=Anton&family=PT+Sans:wght@400;700&display=swap">
<style>
  :root {
    --stage: #b4b4b4;
    --ink: #111111;
    --orange: #f07a22;
    --lime: #d3eb8a;
    --white: #ffffff;
    --navy-top: #3f4d72;
    --navy-mid: #5d6f95;
    --navy-low: #24345a;
    --sky-top: #8fb6da;
    --sky-low: #e6ecef;
    --sea: #2b4f86;
    --band: #0c0c10;
    --label: #111111;
  }
  * { box-sizing: border-box; margin: 0; padding: 0; }
  html, body { width: 1200px; height: 1200px; overflow: hidden; }
  body {
    background: var(--stage);
    font-family: "PT Sans", sans-serif;
    position: relative;
  }
  .cover {
    position: absolute;
    top: 190px;
    width: 440px;
    height: 660px;
    overflow: hidden;
    box-shadow: 0 10px 30px rgba(0,0,0,0.25);
  }
  .cover--one { left: 110px; }
  .cover--two { left: 650px; }

  .cover__photo { position: absolute; inset: 0; }
  .cover--one .cover__photo {
    background:
      radial-gradient(ellipse 34% 48% at 52% 70%, #1a1d2b 0 92%, transparent 100%),
      linear-gradient(180deg, var(--sky-top) 0%, var(--sky-low) 45%, #c9d4dc 56%, var(--sea) 60%, #3e6aa3 72%, #d4e0ec 78%, var(--sea) 85%);
  }
  .cover--two .cover__photo {
    background:
      radial-gradient(ellipse 23% 52% at 26% 74%, #0f1422 0 92%, transparent 100%),
      linear-gradient(180deg, var(--navy-top) 0%, var(--navy-mid) 38%, #8895b2 50%, var(--navy-low) 62%, #1b2646 100%);
  }
  .cover__band {
    position: absolute;
    left: 0; right: 0; bottom: 0;
    height: 240px;
    background: var(--band);
  }

  .cover__kicker {
    position: absolute;
    top: 32px; left: 0; right: 0;
    text-align: center;
    font-size: 16px;
  }
  .cover__kicker b { font-weight: 700; }
  .cover--one .cover__kicker { color: var(--ink); }
  .cover--two .cover__kicker { color: var(--lime); }

  .cover__author {
    position: absolute;
    top: 56px; left: 0; right: 0;
    text-align: center;
    font-weight: 700;
    line-height: 1;
  }
  .cover--one .cover__author { color: var(--orange); font-size: 40px; }
  .cover--two .cover__author { color: var(--white); font-size: 30px; top: 62px; }

  .cover__subtitle {
    position: absolute;
    font-size: 16px;
    line-height: 1.3;
    text-align: center;
    white-space: nowrap;
  }
  .cover--one .cover__subtitle {
    top: 322px; left: 70px; width: 290px;
    color: var(--white);
  }
  .cover--two .cover__subtitle {
    top: 212px; left: 252px; width: 170px;
    font-size: 15px;
    color: var(--ink);
  }

  .cover__title {
    position: absolute;
    left: 0; right: 0;
    text-align: center;
    font-family: "Anton", sans-serif;
    text-transform: uppercase;
    line-height: 0.98;
  }
  .cover__title .the { font-size: 34px; text-transform: none; margin-right: 6px; }
  .cover__title .line { display: block; font-size: 60px; }
  .cover--one .cover__title { bottom: 40px; color: var(--orange); }
  .cover--two .cover__title { bottom: 160px; color: var(--lime); }

  .option-label {
    position: absolute;
    top: 975px;
    width: 440px;
    text-align: center;
    font-size: 90px;
    color: var(--label);
    line-height: 1;
  }
  .option-label--one { left: 110px; }
  .option-label--two { left: 650px; }
</style>
</head>
<body>

<section class="cover cover--one">
  <div class="cover__photo" role="img" aria-label="Photo of a man seen from behind looking out over the ocean under a bright sky"></div>
  <div class="cover__band"></div>
  <p class="cover__kicker">From the Best Selling Author of “<b>Daybreak</b>”</p>
  <h2 class="cover__author">Norman Quillfeather</h2>
  <p class="cover__subtitle">How this<br>ANCIENT WISDOM<br>is HELPING billionaires, industry<br>icons and entrepreneurs TO BE<br>BETTER LEADERS, increase<br>impact and leave a legacy</p>
  <h1 class="cover__title"><span class="line"><span class="the">The</span>Harvest of</span><span class="line">Quiet Builders</span></h1>
</section>

<section class="cover cover--two">
  <div class="cover__photo" role="img" aria-label="Dusky blue photo of a man seen from behind looking out over the sea"></div>
  <p class="cover__kicker">From the Best Selling Author of “<b>Daybreak</b>”</p>
  <h2 class="cover__author">Norman Quillfeather</h2>
  <p class="cover__subtitle">How this ancient wisdom<br>is helping billionaires,<br>industry icons and<br>entrepreneurs to be<br>better leaders,<br>increase impact<br>and leave a legacy</p>
  <h1 class="cover__title"><span class="line"><span class="the">The</span>Harvest of</span><span class="line">Quiet Builders</span></h1>
</section>

<div class="option-label option-label--one">1</div>
<div class="option-label option-label--two">2</div>

</body>
</html>
```